BRV Early College and Career Program

Starting a new program initiative at Birchmont Valley School where students will have the opportunity to take college courses during their senior year of high school. Preferably add some pictures to reflect the career pathways we are offering (below) Some context to use for this flyer are:

Learn more about the career focused courses in…
• Education
• Computer & Information Science
• Technology & Engineering
• Health

Things to look forward to:
Experience college in high school
Finish college early
Save money on college tuition and fees
Advice on Career pathways

all classes fit into OPAL CREDIT BUNDLE

For more information contact

Gavin Purdy - ZT12 Alliances -WHVC
555.014.2291
Email: gpurdy@whvc-example.edu

Ms. Okafuji- Early College Coordinator
Email: dena.okafuji@birchmont-example.org
Room J215

I uploaded 5 or so photos that I would like to see incorporated in the design of the flier- using real students from our high school will give a more realistic approach- thanks, Added Monday, August 21, 2017

Target Market(s)

High school students who are currently in 10th grade (for recruitment) and only high school juniors and seniors are able to apply.

Industry/Entity Type

School

Colors

Designer to choose colors to be used in the design.

Requirements
Must have
• logos- some pictures reflecting the different career pathways and the contact information provided. Looking to also have this in a format that I can print on card stock paper not just full length page- ADD / USE photos attached to see which one fits the project better.
Nice to have
• suitable for high school students- attractive
Should not have
• Do not include any generic phone numbers.

```html
<!DOCTYPE html>
<html lang="en">
<head>
<meta charset="utf-8">
<title>BRV Early College Program</title>
<link rel="stylesheet" href="https://fonts.googleapis.com/css2?family=Source+Sans+3:wght@400;600;700&display=swap">
<style>
  :root{
    --navy:#173763;
    --blue:#3d74bf;
    --sky:#4f8ccf;
    --ring:#c8ccd2;
    --grey:#cfd2d6;
    --ink:#555b63;
    --pale:#dbe4f2;
    --white:#ffffff;
  }
  *{margin:0;padding:0;box-sizing:border-box}
  html,body{width:992px;height:1200px;overflow:hidden;background:#fff}
  body{font-family:"Source Sans 3",sans-serif}
  .flyer{position:relative;width:992px;height:1200px;overflow:hidden;background:var(--white)}
  .backdrop{position:absolute;inset:0}
  .abs{position:absolute}
  .brand{display:flex;align-items:center;gap:8px;color:var(--navy);font-weight:600;font-size:19px;line-height:1.05}
  .brand .mark{width:16px;height:16px;background:var(--blue);flex:none}
  .brand-school{left:467px;top:76px;width:240px}
  .brand-college{left:729px;top:66px;width:250px}
  .title{left:570px;top:205px;width:330px;text-align:center;color:var(--white);font-weight:600;font-size:38px;line-height:1.22}
  .tagline{left:613px;top:370px;width:330px;text-align:center;color:var(--navy);font-weight:600;font-size:21px;line-height:1.35}
  .perks{left:36px;top:524px}
  .perks h2{color:var(--navy);font-size:20px;font-weight:700;margin-bottom:6px}
  .perks li{list-style:none;color:var(--ink);font-size:20px;line-height:29px;display:flex;align-items:center;gap:9px}
  .perks li::before{content:"";width:13px;height:13px;border-radius:50%;background:var(--blue);flex:none}
  .path-label{color:var(--white);font-weight:600;font-size:19px;text-align:center;line-height:1.35;width:240px}
  .contact-bar{left:550px;top:906px;width:442px;height:47px;display:flex;align-items:center;justify-content:center;
    color:var(--white);font-size:19px;padding-left:24px}
  .contact{top:1020px;font-size:17px;line-height:25px;color:var(--pale)}
  .contact strong{display:block;color:var(--white);font-size:21px;font-weight:600;margin-bottom:2px}
  .contact .mail{display:flex;align-items:center;gap:6px;font-size:16px}
  .contact .mail svg{flex:none}
  .credit-note{left:666px;top:1020px;width:290px;font-size:17px;line-height:25px;color:var(--pale)}
  .credit-note strong{display:block;color:var(--white);font-size:21px;font-weight:600;margin-top:2px}
</style>
</head>
<body>
<main class="flyer">
  <svg class="backdrop" width="992" height="1200" viewBox="0 0 992 1200">
    <defs>
      <linearGradient id="photoTone" x1="0" y1="0" x2="1" y2="1">
        <stop offset="0" stop-color="#b9a79a"/>
        <stop offset="0.5" stop-color="#7d7c86"/>
        <stop offset="1" stop-color="#4d5468"/>
      </linearGradient>
      <filter id="lift" x="-20%" y="-20%" width="140%" height="150%">
        <feDropShadow dx="0" dy="6" stdDeviation="5" flood-color="#0b1d38" flood-opacity="0.45"/>
      </filter>
    </defs>
    <polygon points="0,0 294,0 608,505 0,505" fill="url(#photoTone)" role="img" aria-label="Photo of two students holding up program backpacks"/>
    <polygon points="294,0 326,0 640,505 608,505" fill="var(--blue)"/>
    <polygon points="326,0 338,0 652,505 640,505" fill="var(--grey)"/>
    <polygon points="458,200 992,200 992,347 548,347" fill="var(--navy)"/>
    <polygon points="456,196 992,196 992,203 460,203" fill="var(--sky)"/>
    <polygon points="547,344 992,344 992,351 551,351" fill="var(--sky)"/>
    <polygon points="0,795 992,508 992,530 0,860" fill="var(--sky)"/>
    <polygon points="0,860 992,530 992,1200 0,1200" fill="var(--navy)"/>
    <rect x="0" y="1160" width="992" height="9" fill="var(--white)"/>
    <rect x="0" y="1169" width="992" height="31" fill="var(--sky)"/>
    <polygon points="572,906 992,906 992,953 550,953" fill="var(--sky)"/>

    <g filter="url(#lift)">
      <circle cx="139" cy="803" r="86" fill="var(--ring)"/>
      <circle cx="139" cy="803" r="78" fill="var(--sky)"/>
      <circle cx="386" cy="749" r="86" fill="var(--ring)"/>
      <circle cx="386" cy="749" r="78" fill="var(--sky)"/>
      <circle cx="614" cy="664" r="86" fill="var(--ring)"/>
      <circle cx="614" cy="664" r="78" fill="var(--sky)"/>
      <circle cx="857" cy="578" r="86" fill="var(--ring)"/>
      <circle cx="857" cy="578" r="78" fill="var(--sky)"/>
    </g>
    <g fill="#fff">
      <polygon points="139,768 89,786 139,804 189,786"/>
      <path d="M111,797 v22 q28,14 56,0 v-22 l-28,10 z"/>
      <rect x="182" y="787" width="3" height="38"/>
      <rect x="179" y="822" width="9" height="14" rx="2"/>
    </g>
    <g fill="none" stroke="#fff">
      <circle cx="366" cy="728" r="13" stroke-width="9" stroke-dasharray="5 3.2"/>
      <circle cx="366" cy="728" r="7" stroke-width="5"/>
      <circle cx="343" cy="757" r="8" stroke-width="6" stroke-dasharray="4 2.3"/>
      <rect x="370" y="742" width="52" height="34" rx="2" stroke-width="5"/>
    </g>
    <rect x="352" y="779" width="84" height="6" rx="2" fill="#fff"/>
    <g>
      <circle cx="610" cy="665" r="30" fill="none" stroke="#fff" stroke-width="16" stroke-dasharray="9 6"/>
      <circle cx="610" cy="665" r="27" fill="#fff"/>
      <circle cx="610" cy="665" r="14" fill="var(--sky)"/>
      <ellipse cx="617" cy="665" rx="36" ry="14" fill="none" stroke="#fff" stroke-width="3" transform="rotate(-30 617 665)"/>
      <ellipse cx="617" cy="665" rx="36" ry="14" fill="none" stroke="#fff" stroke-width="3" transform="rotate(40 617 665)"/>
    </g>
    <g fill="#fff">
      <rect x="845" y="535" width="24" height="82" rx="3"/>
      <rect x="816" y="564" width="82" height="24" rx="3"/>
    </g>
  </svg>

  <div class="abs brand brand-school"><span class="mark"></span>Birchmont Valley Public Schools</div>
  <div class="abs brand brand-college"><span class="mark"></span>Westhaven Valley Community College</div>

  <h1 class="abs title">BRV Early College Program</h1>
  <p class="abs tagline">Earn credit for both High School and College and Learn more about the career focused courses in</p>

  <section class="abs perks">
    <h2>THINGS TO LOOK FORWARD TO:</h2>
    <ul>
      <li>Experience college in high school</li>
      <li>Finish college early</li>
      <li>Save money on college tuition and fees</li>
      <li>Get advice on your future career</li>
    </ul>
  </section>

  <p class="abs path-label" style="left:19px;top:898px">EDUCATION</p>
  <p class="abs path-label" style="left:266px;top:844px">COMPUTER &amp;<br>INFORMATION SCIENCE</p>
  <p class="abs path-label" style="left:491px;top:762px">TECHNOLOGY &amp;<br>ENGINEERING</p>
  <p class="abs path-label" style="left:733px;top:675px">HEALTH</p>

  <div class="abs contact-bar">FOR MORE INFORMATION CONTACT</div>

  <div class="abs contact" style="left:51px">
    <strong>Gavin Purdy</strong>
    ZT12 Alliances<br>WHVC<br>555.014.2291
    <span class="mail"><svg width="14" height="10" viewBox="0 0 14 10"><rect width="14" height="10" fill="var(--sky)"/><path d="M0,0 L7,6 L14,0" fill="none" stroke="#173763" stroke-width="1.2"/></svg>gpurdy@whvc-example.edu</span>
  </div>
  <div class="abs contact" style="left:329px">
    <strong>Ms. Okafuji</strong>
    Early College Coordinator<br>Room J215
    <span class="mail"><svg width="14" height="10" viewBox="0 0 14 10"><rect width="14" height="10" fill="var(--sky)"/><path d="M0,0 L7,6 L14,0" fill="none" stroke="#173763" stroke-width="1.2"/></svg>dena.okafuji@birchmont-example.org</span>
  </div>
  <p class="abs credit-note">All classes fit into<strong>OPAL CREDIT BUNDLE</strong></p>
</main>
</body>
</html>
```